Moldran Foods needs a new label for canned pineapple

We want a very tasty (in terms of making your mouth water) and clean design (less is more) for our canned pineapple under the new logo of Moldran Leafline division

Target Market(s)

The company’s mission is to bring quality food to target audiences of any social status (you receive a bit more than what you spend). Our core values are: reliability, loyalty and commitment to development.
The product is sold to mainstream and lower Mainstream customers.

Requirements
Must have
• The design should take into consideration the visibility on the shelf among competitor products (brief file) and that the product is a MAINSTREAM product.
We want a very tasty (in terms of making your mouth water) and clean design (less is more). The design should be easily modifiable for other canned fruits or vegetables.
The package must display on the front the following elements listed in the order of their should have noticeability:
• Moldran Leaf logo
• Pineapple picture
• Product name
Designers should take into account that the shelfs for displaying the products in the shops may have an elevation of up to 3 cm that can overlap the product label.

Guidelines
• We would like the packaging to be as simple as possible (or at least not to sabotage the Moldran name ), as our strategy depends on the agressive communication of the Moldran logo.
• We would also like to communicate through suggestive and optimal colours as to be easily spotted on the shelf.
• As we have quite a minimal communication budget we need basically for the packaging to do a lot of the communication job itself
• FMCG is a highly visual industry so we have to include pictures of the products on the packages (even more than others do, as we are focused on health and quality - we want people to have that feeling of fresh products even though we are selling canned ones)
Should not have
• but the minimum amount of text on the front.

```html
<!DOCTYPE html>
<html lang="ro">
<head>
<meta charset="utf-8">
<title>Moldran Leafline – Ananas, etichetă spate</title>
<link href="https://fonts.googleapis.com/css2?family=PT+Sans+Narrow:wght@400;700&family=PT+Sans:wght@400&display=swap" rel="stylesheet">
<style>
  :root {
    --page-bg: #ececec;
    --sky-top: #bcd9ee;
    --sky-mid: #6fb4e2;
    --mist: #dfeef3;
    --leaf-light: #b8dc5a;
    --leaf: #86c43a;
    --leaf-deep: #6fb22c;
    --rim: #a9b83a;
    --rim-base: #b9bcbe;
    --ink-green: #173f12;
    --table-bg: #0f4a1c;
    --table-line: #d8d24a;
    --table-text: #f3e98a;
    --fruit-gold: #c9a43a;
    --fruit-leaf: #5d8f2c;
  }
  html, body {
    margin: 0;
    width: 1200px;
    height: 1200px;
    overflow: hidden;
    background: var(--page-bg);
  }
  .canvas {
    position: relative;
    width: 1200px;
    height: 1200px;
  }
  .label {
    position: absolute;
    left: 260px;
    top: 170px;
    width: 650px;
    height: 850px;
    overflow: hidden;
    background: linear-gradient(180deg,
      var(--sky-top) 0%,
      var(--sky-mid) 14%,
      var(--mist) 38%,
      var(--leaf-light) 62%,
      var(--leaf) 80%,
      var(--leaf-deep) 100%);
  }
  .label__rim {
    position: absolute;
    left: 0; right: 0;
    height: 12px;
    background: var(--rim);
  }
  .label__rim--top { top: 0; }
  .label__rim--bottom { bottom: 0; background: var(--rim-base); }
  .fruit-visual {
    position: absolute;
    left: 615px;
    top: 310px;
    width: 35px;
    height: 510px;
    background: linear-gradient(180deg, var(--fruit-leaf) 0%, var(--fruit-leaf) 30%, var(--fruit-gold) 55%, #a88a2c 80%, var(--fruit-leaf) 100%);
    opacity: 0.85;
    border-radius: 18px 0 0 18px;
  }
  .text-block {
    position: absolute;
    left: 0;
    width: 680px;
    text-align: center;
    font-family: "PT Sans Narrow", sans-serif;
    font-weight: 700;
    color: var(--ink-green);
  }
  .heading { font-size: 25px; letter-spacing: 0.5px; margin: 0; }
  .body-line { font-size: 23px; margin: 2px 0 0; }
  .ingredients { top: 58px; }
  .nutrition-info { top: 152px; }
  .nutrition-info .body-line { margin-top: 6px; }
  .per-serving { top: 280px; }
  .serving-tip { top: 680px; }
  .serving-tip .body-line { margin-top: 6px; }
  .nutrition-table {
    position: absolute;
    left: 130px;
    top: 320px;
    width: 413px;
    border-collapse: collapse;
    background: var(--table-bg);
    font-family: "PT Sans", sans-serif;
    font-size: 18px;
    color: var(--table-text);
  }
  .nutrition-table td {
    border: 1.5px solid var(--table-line);
    padding: 2px 9px;
    vertical-align: top;
    line-height: 26px;
  }
  .nutrition-table .col-name { width: 242px; }
  .nutrition-table .col-amount { width: 66px; }
  .spread { display: inline-block; margin-left: 36px; }
  .spread--tight { margin-left: 20px; }
</style>
</head>
<body>
<div class="canvas">
  <section class="label">
    <div class="label__rim label__rim--top"></div>
    <div class="fruit-visual" role="img" aria-label="Fotografie cu un ananas proaspăt, cu frunze verzi"></div>

    <div class="text-block ingredients">
      <p class="heading">INGREDIENTE</p>
      <p class="body-line">Ananas(60.20%), Apă(31.7%), Zahăr(8%), Acid Citric(0.10%)</p>
    </div>

    <div class="text-block nutrition-info">
      <p class="heading">INFORMAȚII NUTRIȚIONALE</p>
      <p class="body-line">O porție: ½ cană (140g)</p>
      <p class="body-line">Porții/cutie – aprox. 4</p>
    </div>

    <div class="text-block per-serving">
      <p class="heading">CANTITATE/ PORȚIE</p>
    </div>

    <table class="nutrition-table">
      <tr><td colspan="3">Calorii 80 <span class="spread">Acizi grași 0</span></td></tr>
      <tr><td class="col-name">Lipide<br>Din care Lipide saturate</td><td class="col-amount">0g<br>0g</td><td>0%<br>0%</td></tr>
      <tr><td>Colesterol</td><td>0g</td><td>0%</td></tr>
      <tr><td>Sodiu</td><td>10mg</td><td>0%</td></tr>
      <tr><td>Carbohidrați<br>Fibre<br>Zaharuri</td><td>20g<br>&lt;1g<br>17g</td><td>6%<br>0%</td></tr>
      <tr><td>Proteine</td><td>0g</td><td></td></tr>
      <tr><td colspan="3">Vitamina A 0% <span class="spread">Vitamina C 2%</span> <span class="spread spread--tight">Calciu 2%</span><br>Fier 2%</td></tr>
    </table>

    <div class="text-block serving-tip">
      <p class="heading">SUGESTIE DE SERVIRE</p>
      <p class="body-line">A se servi simplu sau împreună cu prăjituri și produse de patiserie.</p>
      <p class="body-line">Poate servi pentru marinarea cărnii.</p>
      <p class="body-line">Perfect pentru piureuri din fructe.</p>
    </div>

    <div class="label__rim label__rim--bottom"></div>
  </section>
</div>
</body>
</html>
```